Bramblewood Card Company Business Cards

We are a trading card store with Glimmorax, sports and other TCG cards, we need a business card design that encompasses a clean cut, modern style with a retro flare. website is bramblewoodcardco.com for reference. Can utilize a comic book era feel or a more modern outdoor feel to utilize the "Pacific Northwest" elements of tress, mountains, etc.

Industry/Entity Type

Trading cards and collectibles

Contact Information for Business Card

business name, email address, phone number, name, owner job title

Font styles to use
Sans Serif

```html
<!DOCTYPE html>
<html lang="en">
<head>
<meta charset="utf-8">
<title>Bramblewood Card Company – Business Cards</title>
<link href="https://fonts.googleapis.com/css2?family=Montserrat:wght@400;500;700;800&display=swap" rel="stylesheet">
<style>
  :root {
    --backdrop: #2b2b2b;
    --brand-blue: #14c0e1;
    --brand-grey: #6d6d6d;
    --card-white: #ffffff;
    --ink: #1f1f1f;
  }
  * { margin: 0; padding: 0; box-sizing: border-box; }
  html, body { width: 1200px; height: 875px; overflow: hidden; }
  body {
    background: var(--backdrop);
    font-family: "Montserrat", sans-serif;
    display: flex;
    align-items: center;
    justify-content: center;
    gap: 40px;
  }
  .card {
    width: 540px;
    height: 310px;
    position: relative;
  }
  .card--front {
    background: var(--brand-blue);
    display: flex;
    align-items: center;
    justify-content: center;
  }
  .brand-mark {
    display: flex;
    align-items: center;
    gap: 12px;
    color: var(--brand-grey);
    font-weight: 800;
    text-transform: uppercase;
  }
  .brand-mark__dot {
    border-radius: 50%;
    background: var(--brand-grey);
    flex: none;
  }
  .card--front .brand-mark { font-size: 26px; line-height: 1.15; max-width: 300px; }
  .card--front .brand-mark__dot { width: 34px; height: 34px; }

  .card--back {
    background: var(--card-white);
    color: var(--ink);
  }
  .card--back .brand-mark {
    position: absolute;
    top: 34px;
    right: 36px;
    font-size: 13px;
    line-height: 1.2;
    max-width: 170px;
  }
  .card--back .brand-mark__dot { width: 18px; height: 18px; }

  .holder {
    position: absolute;
    left: 40px;
    top: 120px;
  }
  .holder__name {
    color: var(--brand-blue);
    font-weight: 700;
    font-size: 26px;
    line-height: 1.05;
  }
  .holder__title {
    font-size: 13px;
    font-weight: 400;
    margin-top: 2px;
  }
  .address {
    position: absolute;
    right: 36px;
    top: 150px;
    font-size: 12.5px;
    line-height: 1.35;
    text-align: left;
  }
  .contacts {
    position: absolute;
    left: 40px;
    bottom: 30px;
    list-style: none;
    font-size: 12.5px;
    line-height: 1.5;
  }
  .contacts li { display: flex; align-items: center; gap: 9px; }
  .contacts svg { width: 12px; height: 12px; fill: var(--brand-blue); flex: none; }
</style>
</head>
<body>
  <section class="card card--front" aria-label="Card front">
    <div class="brand-mark">
      <span class="brand-mark__dot"></span>
      <span>Bramblewood Card Company</span>
    </div>
  </section>

  <section class="card card--back" aria-label="Card back">
    <div class="brand-mark">
      <span class="brand-mark__dot"></span>
      <span>Bramblewood Card Company</span>
    </div>

    <div class="holder">
      <p class="holder__name">Dorian Hale</p>
      <p class="holder__title">Owner</p>
    </div>

    <p class="address">2874 Cedar Hollow Rd Suite210<br>Ridgefield, Ohio 44187</p>

    <ul class="contacts">
      <li>
        <svg viewBox="0 0 24 24" aria-hidden="true"><path d="M6.6 10.8a15.1 15.1 0 0 0 6.6 6.6l2.2-2.2a1 1 0 0 1 1-.25 11.4 11.4 0 0 0 3.6.57 1 1 0 0 1 1 1V20a1 1 0 0 1-1 1A17 17 0 0 1 3 4a1 1 0 0 1 1-1h3.5a1 1 0 0 1 1 1c0 1.25.2 2.45.57 3.57a1 1 0 0 1-.25 1z"/></svg>
        06-48213579
      </li>
      <li>
        <svg viewBox="0 0 24 24" aria-hidden="true"><path d="M2 5h20v14H2z M3.5 6.5 12 13l8.5-6.5" fill="none" stroke="#14c0e1" stroke-width="2"/><path d="M2 5h20l-10 8z"/></svg>
        info@bramblewoodcardcompany.com
      </li>
      <li>
        <svg viewBox="0 0 24 24" aria-hidden="true"><path d="M12 2a10 10 0 1 0 0 20 10 10 0 0 0 0-20zm6.9 6h-2.9a15.7 15.7 0 0 0-1.4-3.6A8 8 0 0 1 18.9 8zM12 4c.8 1.2 1.5 2.5 1.9 4h-3.8c.4-1.5 1.1-2.8 1.9-4zM4.3 14a8 8 0 0 1 0-4h3.4a16 16 0 0 0 0 4zm.8 2h2.9c.3 1.3.8 2.5 1.4 3.6A8 8 0 0 1 5.1 16zM8 8H5.1a8 8 0 0 1 4.3-3.6C8.8 5.5 8.3 6.7 8 8zm4 12c-.8-1.2-1.5-2.5-1.9-4h3.8c-.4 1.5-1.1 2.8-1.9 4zm2.3-6H9.7a14.7 14.7 0 0 1 0-4h4.6a14.7 14.7 0 0 1 0 4zm.3 5.6c.6-1.1 1.1-2.3 1.4-3.6h2.9a8 8 0 0 1-4.3 3.6zm1.7-5.6a16 16 0 0 0 0-4h3.4a8 8 0 0 1 0 4z"/></svg>
        www.bramblewoodcardcompany.com
      </li>
    </ul>
  </section>
</body>
</html>
```